K7 Services business card design contest. Use logo and create a professional layout.

See attached sample. Please sharpen all text and images, don't want any pix-elated content. We are looking for a clean look that quickly provides the information need. Please include our information provided on the sample card. Please feel free to offer any design changes. Please only user the colors provided: #2D3539 & #FFA500. Do not prefer any images other than the K7 Logo

Target Market(s)

Construction, Architects, General Contractors, residential

Industry/Entity Type

Business

Contact Information for Business Card

Company logo, Name, email, fax & phone

Font styles to use
Other font styles liked:
• Josefin Slab

Requirements
Must have
• Name
• Phone & Fax #'s
• address
• Logo
• Website url: www.kq7services.example
Nice to have
• Font Colors #2D3539 & #FFA400
• We prefer a white background.

```html
<!DOCTYPE html>
<html lang="en">
<head>
<meta charset="utf-8">
<title>K7 Services – Business Card</title>
<link href="https://fonts.googleapis.com/css2?family=Montserrat:wght@400;500;600&display=swap" rel="stylesheet">
<style>
  :root {
    --ink: #2D3539;
    --orange: #F0962A;
    --orange-soft: #F5A445;
    --paper: #FFFFFF;
    --backdrop: #E4E4E4;
  }
  * { margin: 0; padding: 0; box-sizing: border-box; }
  html, body { width: 1200px; height: 852px; overflow: hidden; }
  body {
    background: var(--backdrop);
    font-family: "Montserrat", Arial, sans-serif;
    color: var(--ink);
    position: relative;
  }
  .card {
    position: absolute;
    width: 560px;
    height: 320px;
    border-radius: 14px;
    overflow: hidden;
    box-shadow: 0 6px 18px rgba(0,0,0,0.18);
  }

  /* Brand name: one colour, one weight, one plain square */
  .brand { display: flex; align-items: center; gap: 12px; }
  .brand-mark { width: 16px; height: 16px; background: var(--ink); flex: none; }
  .brand-name {
    font-weight: 600; font-size: 40px; line-height: 1; color: var(--ink);
    white-space: nowrap;
  }
  .tagline {
    font-weight: 400; font-size: 15px; color: var(--ink);
    letter-spacing: 1.5px; text-transform: uppercase; white-space: nowrap;
  }

  /* Front */
  .card-front {
    left: 70px; top: 80px;
    background: linear-gradient(135deg, var(--orange) 0%, var(--orange-soft) 100%);
    display: flex; flex-direction: column; align-items: center; justify-content: center;
    gap: 22px;
  }

  /* Back */
  .card-back {
    left: 570px; top: 452px;
    background: repeating-linear-gradient(90deg, #FFFFFF 0 6px, #F7F7F7 6px 7px);
  }
  .card-back .brand { position: absolute; left: 230px; top: 44px; gap: 10px; }
  .card-back .brand-name { font-size: 30px; }
  .card-back .brand-mark { width: 13px; height: 13px; }
  .card-back .tagline { position: absolute; left: 253px; top: 88px; font-size: 11px; }

  .name-band {
    position: absolute; left: 0; top: 140px;
    width: 330px; height: 78px;
    background: var(--orange);
    border-radius: 0 16px 16px 0;
    padding: 16px 0 0 30px;
    color: var(--paper);
  }
  .person-name {
    font-size: 17px; font-weight: 500; letter-spacing: 2px; text-transform: uppercase;
    white-space: nowrap;
  }
  .person-title { font-size: 13px; margin-top: 6px; }

  .contact-list {
    position: absolute; left: 30px; top: 236px;
    list-style: none; font-size: 13px;
  }
  .contact-list li { display: flex; align-items: center; gap: 10px; height: 22px; white-space: nowrap; }
  .contact-list svg { width: 13px; height: 13px; fill: var(--orange); flex: none; }

  .services-block {
    position: absolute; left: 350px; top: 146px;
    font-size: 11.5px; line-height: 1.7; white-space: nowrap;
  }
  .services-list { color: var(--orange); font-size: 12px; letter-spacing: 0.5px; margin-bottom: 2px; }
</style>
</head>
<body>
  <section class="card card-front">
    <div class="brand">
      <span class="brand-mark"></span>
      <span class="brand-name">K7 Services</span>
    </div>
    <p class="tagline">Clarity From Every Angle</p>
  </section>

  <section class="card card-back">
    <div class="brand">
      <span class="brand-mark"></span>
      <span class="brand-name">K7 Services</span>
    </div>
    <p class="tagline">Clarity From Every Angle</p>

    <div class="name-band">
      <p class="person-name">Marcus D. Hale, MBA</p>
      <p class="person-title">Director of Operations</p>
    </div>

    <ul class="contact-list">
      <li>
        <svg viewBox="0 0 24 24" aria-hidden="true"><path d="M6.6 10.8c1.4 2.8 3.8 5.1 6.6 6.6l2.2-2.2c.3-.3.7-.4 1-.2 1.1.4 2.3.6 3.6.6.6 0 1 .4 1 1V20c0 .6-.4 1-1 1C10.6 21 3 13.4 3 4c0-.6.4-1 1-1h3.5c.6 0 1 .4 1 1 0 1.3.2 2.5.6 3.6.1.3 0 .7-.2 1l-2.3 2.2z"/></svg>
        (404) 555 - 0142
      </li>
      <li>
        <svg viewBox="0 0 24 24" aria-hidden="true"><path d="M6 2h9l3 3v5H6V2zm2 2v4h8V6h-2V4H8zM3 11h18v9H3v-9zm3 3v2h4v-2H6zm8 0v2h4v-2h-4z"/></svg>
        (404) 555 - 0187
      </li>
      <li>
        <svg viewBox="0 0 24 24" aria-hidden="true"><path d="M12 2a10 10 0 100 20 10 10 0 000-20zm0 2c.8 1.2 1.5 2.5 1.9 4h-3.8c.4-1.5 1.1-2.8 1.9-4zM4.3 14a8 8 0 010-4h3.4a16 16 0 000 4H4.3zm5.4 0a14 14 0 010-4h4.6a14 14 0 010 4H9.7zm6.6 0a16 16 0 000-4h3.4a8 8 0 010 4h-3.4zM12 20c-.8-1.2-1.5-2.5-1.9-4h3.8c-.4 1.5-1.1 2.8-1.9 4z"/></svg>
        www.kq7services.example
      </li>
    </ul>

    <div class="services-block">
      <p class="services-list">DRONE | WEBCAM | VIDEO</p>
      <p>2710 Ridgefield Road, Suite</p>
      <p>214-118 Alpharetta, Georgia, 30005</p>
    </div>
  </section>
</body>
</html>
```